House Cleaning Platform for Consumers and Cleaners

UPDATE: I've attached screenshots showing a purchase flow example, something all designers have missed in their designs. PLEASE check the URLs I've included in the brief for examples of a cleaning website. I've seen mostly landing pages and nothing else.

WHAT I'M LOOKING FOR:
I need the UI designed for a house cleaning web platform from 2 separate experiences: one from the consumer end to order a cleaner to come clean their house and one from a cleaner’s end that manages their orders and manages their schedule.

The UI will need to include photo uploading for before and after photos, a checkout/cart experience w/ tips, toggle options for adding and removing rooms/extras cleaning add-ons, customer+cleaner reviews (meaning the cleaner finished the job and they can rate and review the customer as well as the customer can rate and review the cleaner), order history for consumers, job history for cleaners, profile, settings, and landing pages for both.

PLEASE DO NOT USE THE COLOR BLUE AS THE PRIMARY COLOR. Use a light green (HEX #2fdf86) instead for primary theming color.

REFERENCES:
If you'd like a few websites I've enjoyed for references, checkout:
larkpolish.example, vomby.example, and brightfernhome.example.

For sake of branding, the company name is PlumNest. Currently do not have a logo as we have not decided on the name. Logo will come later.

Feel free to reach out to me if you have any questions!
Updates

Most designer submissions were a landing page and only a landing page. Very few designed the flows I requested and none designed a schedule management page. I even updated the Brief to more clearly outline the needs and references. Only about 2-3 of the designers actually did more than a landing page. Still don't believe I received 6 designers input that I had paid for.

Target Market(s)

FULL-TIME WORKING HOUSEHOLDS, SINGLE PROFESSIONALS, SINGLE PARENTS, ELDERLY & MOBILITY CHALLENGED, BUSY BODIES.

Industry/Entity Type

Cleaning, gig work.

Number of Pages Required

5+ page

Font styles to use
Other font styles liked:
• Jost or Lexend are great Google Font options I've used in the pitch deck and horribly done app mockups.

Colors
00AB8E
00BBA5
67D7C9
C6EFE9
E9F9F6
59FF00
82FF00
B8FF75
E3FFCB
F4FFEA
FFF300
FFF600
FEFA6F
FFFEC7
FFFEE8
FFC000
F8CF3A
FAE287
FDF2CF
FEFAEE

Requirements
Must have
• Landing page, consumer flow, cleaner schedule management, checkout flow, Rate & Review for consumer and/or cleaner, order history, profile.
Nice to have
• I'd like it to be simple in design and modern, but not so simple it's boring. Iconography can sometimes break that up, but I don't want it looking busy. It's a cleaning platform so the UI should look clean.

```html
<!DOCTYPE html>
<html lang="en">
<head>
<meta charset="utf-8">
<title>PlumNest – Cleaning Requests</title>
<link rel="stylesheet" href="https://fonts.googleapis.com/css2?family=Lexend:wght@400;500&family=Open+Sans:wght@400;600;700&display=swap">
<style>
  :root {
    --green: #28d386;
    --orange: #f7941d;
    --ink: #111111;
    --text: #1a1a1a;
    --border: #b5b5b5;
    --light-border: #d6d6d6;
    --bg: #ffffff;
  }
  * { box-sizing: border-box; margin: 0; padding: 0; }
  html, body { width: 1200px; height: 654px; overflow: hidden; background: var(--bg); }
  body { position: relative; font-family: "Open Sans", sans-serif; color: var(--text); }

  .brand {
    position: absolute; left: 101px; top: 16px;
    font: 700 32px/1 "Open Sans", sans-serif; color: var(--green); letter-spacing: -0.3px;
  }
  .nav a {
    position: absolute; top: 27px;
    font: 400 12px/16px "Lexend", sans-serif; color: var(--ink); text-decoration: none;
  }
  .search {
    position: absolute; left: 731px; top: 22.5px; width: 219px; height: 25px;
    border: 1px solid var(--light-border); border-radius: 13px;
    display: flex; align-items: center; padding-left: 7px;
    font: 400 12px "Lexend", sans-serif; color: var(--ink);
  }
  .search svg { margin-right: 15px; }
  .login { left: 981px; }
  .signup {
    position: absolute; left: 1024px; top: 22.5px; width: 75px; height: 25px;
    background: var(--green); border-radius: 13px;
    font: 400 10.5px/25px "Lexend", sans-serif; text-align: center; color: var(--ink);
  }

  .page-title {
    position: absolute; left: 0; right: 0; top: 126px; text-align: center;
    font: 700 39px/1.2 "Open Sans", sans-serif; color: var(--ink); letter-spacing: -0.2px;
  }
  .divider { position: absolute; left: 0; right: 0; top: 202px; height: 1px; background: var(--green); }

  .request-intro {
    position: absolute; left: 101px; top: 257px;
    font: 400 16px/22px "Open Sans", sans-serif; color: var(--ink);
  }
  .request-intro strong { font-weight: 700; }
  .request-intro .profile-link { color: var(--orange); font-size: 11.5px; font-weight: 600; margin-left: 10px; }

  .field { position: absolute; width: 312.5px; }
  .field label { display: block; font: 600 11.5px/16px "Open Sans", sans-serif; color: var(--ink); }
  .field .value {
    margin-top: 14px; height: 31px; border: 1px solid var(--border); border-radius: 2px;
    padding-left: 14px; font: 400 11px/29px "Lexend", sans-serif; color: var(--ink);
  }
  .col1 { left: 101px; } .col2 { left: 443px; } .col3 { left: 785px; }
  .row1 { top: 306px; } .row2 { top: 387px; }

  .btn {
    position: absolute; top: 511px; width: 175px; height: 50px; border-radius: 25px;
    font: 500 16px/50px "Open Sans", sans-serif; text-align: center; color: var(--ink); font-weight: 600;
  }
  .btn-accept { left: 101px; background: var(--green); }
  .btn-decline { left: 307.5px; border: 1px solid var(--light-border); line-height: 48px; }
</style>
</head>
<body>
  <header>
    <div class="brand">PlumNest</div>
    <nav class="nav">
      <a style="left:438px">Home</a>
      <a style="left:489px">Pricing</a>
      <a style="left:546px">Services</a>
      <a style="left:612px">Contact</a>
      <a style="left:674px">Help</a>
      <a class="login">Login</a>
    </nav>
    <div class="search">
      <svg width="13" height="13" viewBox="0 0 13 13" fill="none" stroke="#111" stroke-width="1">
        <circle cx="5.6" cy="5.6" r="4.8"/><line x1="9.1" y1="9.1" x2="12.3" y2="12.3"/>
      </svg>
      Search
    </div>
    <div class="signup">Sign Up</div>
  </header>

  <h1 class="page-title">Cleaning Requests</h1>
  <div class="divider"></div>

  <main>
    <p class="request-intro"><strong>Wren 2346</strong> has send you a cleaning work request. <span class="profile-link">(View Profile)</span></p>

    <div class="field col1 row1"><label>Zip Code</label><div class="value">12345</div></div>
    <div class="field col2 row1"><label>Total Square Feet At Home</label><div class="value">1200</div></div>
    <div class="field col3 row1"><label>Date Of Cleaning</label><div class="value">22-1-2023</div></div>
    <div class="field col1 row2"><label>Start Time</label><div class="value">8:00am To 12:00pm</div></div>
    <div class="field col2 row2"><label>Email Address</label><div class="value">abcdfh@mailbox.example</div></div>
    <div class="field col3 row2"><label>Contact Number</label><div class="value">1234567890</div></div>

    <div class="btn btn-accept">Accept</div>
    <div class="btn btn-decline">Decline</div>
  </main>
</body>
</html>
```